Exclusive beauty salon needs a price list or services booklet

I need a new very attractive flyer for my beauty salon, containing information on the different services and their prices.
In attachment you can find a pdf of the "old" one, but I'd love to have a beautifully designed new one!
I'd love to have a booklet in format 148 x 148 mm, or in US format, containing 12 or 16 pages, but if you can offer other nice looking designs they are welcome!
The services that need to come in the booklet with their prices can all be found on my website: www.atelierverano.be, starting with
Gelaatsverzorging
Wimperverlenging
Suikerontharing
Wimperlifting
Permanente Make Up
Airbrush Tanning

Target Market(s)

woman from 20 to 89 years old

Industry/Entity Type

Beauty Salon

Font styles to use
Sans Serif

Colors

Designer to choose colors to be used in the design.

Requirements
Must have
• a classy nice look, it must contain details about the services from my beauty salon and their prices, and nice pictures.
• The Names, prices and explanations of the services can easily be found on my website: www.atelierverano.be
Nice to have
• In attachment you can find the "old" price list in pdf, what I need now is a "new booklet" with the new logo and updated services price list.
• I need a very nice and attractive looking booklet, classy chique, Paris chique, looking very expensive.
Should not have
• Not too much colors, not too curly, but still feminine

```html
<!DOCTYPE html>
<html lang="nl">
<head>
<meta charset="utf-8">
<title>Atelier Verano – Prijsboekje</title>
<link href="https://fonts.googleapis.com/css2?family=Open+Sans:ital,wght@0,300;0,400;1,300&display=swap" rel="stylesheet">
<style>
:root{
  --board:#676767;
  --frame:#a3a3a5;
  --page:#ffffff;
  --panel:#a6a6a8;
  --teal:#7ac9d3;
  --teal-soft:rgba(125,205,200,.78);
  --heading:#5bbdc9;
  --text:#8b8b8b;
  --line:#e6e6e6;
}
*{margin:0;padding:0;box-sizing:border-box}
html,body{width:1200px;height:1120px;overflow:hidden}
body{background:var(--board);font-family:"Open Sans",Arial,sans-serif;font-weight:300;color:var(--text);position:relative}
.spread{position:absolute;width:460px;height:166px;box-shadow:0 1px 3px rgba(0,0,0,.35)}
.spread.is-framed{background:var(--frame)}
.spread.is-open{background:var(--page)}
.page{position:absolute;top:6px;width:218px;height:154px;background:var(--page);overflow:hidden}
.page.left{left:6px}
.page.right{left:236px}
.page.grey{background:var(--panel)}
.photo{position:absolute;top:0;bottom:0}
.copy{position:absolute;top:10px;font-size:3.5px;line-height:1.5}
.copy h3{font-weight:400;color:var(--heading);font-size:4.6px;margin:0 0 2px}
.copy p{margin-bottom:3px}
.copy ul{list-style:none;margin-bottom:3px}
.copy li::before{content:"✓ ";color:var(--heading)}
.price-list{list-style:none}
.price-list li{display:flex;justify-content:space-between}
.price-list li::before{content:none}
.price-list span:last-child{color:var(--heading)}
.teal-box{position:absolute;background:var(--teal-soft);color:#fff;font-weight:300;line-height:1.25;padding:3px}
.outline-box{position:absolute;border:.7px solid #d8d8d8;color:#fff;font-size:3.5px;line-height:1.55;padding:7px 8px;font-style:italic}
.outline-box ul{list-style:none}
.outline-box li::before{content:"✓ "}
.wordmark{font-weight:300;letter-spacing:2.2px;text-transform:uppercase;color:#8b8b8b}
.price-note{position:absolute;left:0;right:0;text-align:center;color:#fff;font-size:4.4px;line-height:1.6}
</style>
</head>
<body>

<!-- Cover -->
<section class="spread is-open" style="left:52px;top:53px">
  <div class="page left" style="background:var(--teal)">
    <div style="position:absolute;left:27px;top:53px;width:165px;height:47px;background:#fff;display:flex;align-items:center">
      <div class="wordmark" style="width:92px;text-align:center;font-size:5px">Atelier Verano</div>
      <div style="font-size:3.2px;line-height:1.5;border-left:.6px solid var(--line);padding-left:6px">
        Atelier Verano Schoonheidsinstituut<br>Lindelaan 14<br>9000 Gent<br>0470 12 34 56<br>info@atelierverano.be<br>www.atelierverano.be
      </div>
    </div>
  </div>
  <div class="page right">
    <div class="photo" role="img" aria-label="Close-up portrait photo for the cover" style="left:0;width:151px;background:linear-gradient(120deg,#eadbd4,#d9b8ab 60%,#cfa49a)"></div>
    <div class="wordmark" style="position:absolute;left:158px;top:70px;font-size:4.6px;letter-spacing:1.5px">Atelier Verano</div>
    <div style="position:absolute;right:4px;bottom:4px;font-size:3px;letter-spacing:.4px">www.atelierverano.be</div>
  </div>
</section>

<!-- Welcome -->
<section class="spread is-open" style="left:52px;top:272px">
  <div class="page left grey">
    <div class="outline-box" style="left:47px;top:34px;width:124px;height:80px;padding-top:12px">
      <p style="margin-bottom:4px">Al meer dan 5 jaar sta ik met veel passie en enthousiasme klaar om mijn klanten te ontvangen. Mijn specialiteiten zijn gelaatsverzorgingen met producten van hoge kwaliteit, wimperextensions, suikerontharing en permanente make up.</p>
      <p>Ik volg regelmatig bijscholingen om bij te blijven met de nieuwste trends.</p>
    </div>
  </div>
  <div class="page right">
    <div class="photo" role="img" aria-label="Portrait photo of the beautician in a white uniform" style="left:0;right:0;background:linear-gradient(110deg,#efefef 35%,#e3d2c8 60%,#d8c2b4)"></div>
    <div class="teal-box" style="left:19px;top:35px;width:54px;height:76px;font-size:15px;line-height:1.07">Steeds tot uw dienst</div>
  </div>
</section>

<!-- Permanent make-up -->
<section class="spread is-framed" style="left:52px;top:486px">
  <div class="page left">
    <div class="photo" role="img" aria-label="Beauty portrait with red lips" style="left:0;width:105px;background:linear-gradient(120deg,#f0e4dd,#e2c6b9 55%,#c9a595)"></div>
    <div class="copy" style="left:111px;width:100px;top:9px">
      <h3>Permanente Make Up</h3>
      <p>Permanente make up is altijd goed en zorgt ervoor dat je er altijd verzorgd uitziet, ook zonder dagelijkse moeite of tijd.</p>
      <p>De pigmenten worden zacht in de huid aangebracht zodat het resultaat natuurlijk en subtiel blijft.</p>
      <h3 style="margin-top:8px">Gratis Adviesgesprek</h3>
      <p>Het is mogelijk om eerst een consult te boeken om samen de wensen en de vorm te bespreken.</p>
    </div>
  </div>
  <div class="page right">
    <div class="copy" style="left:6px;width:104px;top:9px">
      <h3>Wanneer is Permanente Make-Up Zinvol?</h3>
      <ul>
        <li>Bij weinig of lichte wenkbrauwen</li>
        <li>Bij een allergie voor gewone make-up</li>
        <li>Bij slechtziendheid of bevende handen</li>
        <li>Voor sporters en actieve vrouwen</li>
        <li>Na chemotherapie of haarverlies</li>
      </ul>
      <h3 style="margin-top:6px">TARIEVEN</h3>
      <ul class="price-list">
        <li><span>Full lips</span><span>€595</span></li>
        <li><span>Permanente make up volledige ooglijn</span><span>€369</span></li>
        <li><span>Brede eyeliner boven het oog</span><span>€235</span></li>
        <li><span>Fijne eyeliner boven</span><span>€186</span></li>
        <li><span>Wenkbrauwen hairstroke</span><span>€320</span></li>
        <li><span>Wenkbrauwen shading</span><span>€320</span></li>
        <li><span>Wenkbrauwen powder brow</span><span>€320</span></li>
      </ul>
    </div>
    <div class="photo" role="img" aria-label="Photo of a permanent make-up treatment on the brows" style="left:114px;right:0;background:linear-gradient(130deg,#f2ebe8,#e3c9bd 60%,#d5b0a2)"></div>
  </div>
</section>

<!-- Facial care brand -->
<section class="spread is-open" style="left:52px;top:695px">
  <div class="page left">
    <div class="photo" role="img" aria-label="Photo of a smiling woman touching her face" style="left:0;right:0;bottom:20px;background:linear-gradient(110deg,#f3eeec 20%,#dcc1b4 55%,#eae4e2)"></div>
    <div class="teal-box" style="left:143px;top:33px;width:55px;height:78px;font-size:7px;line-height:1.65">Een antwoord bieden voor iedere huidconditie, omdat deze uniek is</div>
    <div style="position:absolute;left:0;width:159px;bottom:5px;text-align:center;font-weight:400;font-size:8px;letter-spacing:1px;color:#222">MAISON LUNE</div>
  </div>
  <div class="page right grey">
    <div class="outline-box" style="left:47px;top:34px;width:124px;height:86px">
      <p style="margin-bottom:3px">Het merk Maison Lune heeft een uitgebreid aanbod aan gelaatsverzorgingen, geschikt voor elk huidtype. Na een persoonlijke huidanalyse krijg je advies op maat.</p>
      <p>Maison Lune biedt:</p>
      <ul>
        <li>een huid vol plezier en welzijn</li>
        <li>een unieke ervaring voor de zintuigen</li>
        <li>resultaatgerichte behandelingen</li>
      </ul>
    </div>
  </div>
</section>

<!-- Facial treatments -->
<section class="spread is-framed" style="left:52px;top:903px">
  <div class="page left">
    <div class="photo" role="img" aria-label="Photo of a woman in a yellow dress on a yellow background" style="left:0;width:105px;background:linear-gradient(120deg,#f7c21b,#efa918 55%,#c98a2c)"></div>
    <div class="copy" style="left:111px;width:100px;top:12px;text-align:center">
      <h3>Cosmetische Verzorging</h3>
      <p>Verzorging van de huid met reiniging, peeling en masker, aangepast aan je huidtype.<br><span style="color:var(--heading)">€50</span></p>
      <h3 style="margin-top:16px">Verwijderen van gerstekorrels</h3>
      <p>De prijs is afhankelijk van de hoeveelheid.</p>
      <h3 style="margin-top:20px">Snelle Reiniging</h3>
      <p>Een snelle en diepe reiniging voor een frisse, stralende huid.<br><span style="color:var(--heading)">€59 – 50 min.</span></p>
    </div>
  </div>
  <div class="page right">
    <div class="copy" style="left:6px;width:104px;top:8px;text-align:center">
      <h3>Hydraterende Verzorging</h3>
      <p>Voor een gehydrateerde, volle en frisse huid met langdurig comfort.<br><span style="color:var(--heading)">€55 – 60 min.</span></p>
      <h3 style="margin-top:10px">Zuiverende Verzorging</h3>
      <p>Voor een gemengde tot vette huid die opnieuw in balans moet komen.<br><span style="color:var(--heading)">€65 – 60 min.</span></p>
      <h3 style="margin-top:10px">Luxe Verzorging Rituel Verano</h3>
      <p>Een luxueuze anti-aging verzorging met massage van gezicht, hals en decolleté.<br><span style="color:var(--heading)">€85 – 80 min.</span></p>
    </div>
    <div class="photo" role="img" aria-label="Beauty portrait of a woman with glowing skin" style="left:114px;right:0;background:linear-gradient(120deg,#f4ecea,#e0c5b8 55%,#b88f7e)"></div>
  </div>
</section>

<!-- Sugaring -->
<section class="spread is-framed" style="left:671px;top:53px">
  <div class="page left">
    <div class="photo" role="img" aria-label="Photo of sugaring paste applied to a leg" style="left:0;width:105px;background:linear-gradient(125deg,#f1e4dc,#dfb99f 55%,#d49a6e)"></div>
    <div class="copy" style="left:112px;width:100px;top:9px">
      <h3>Ontharing Met Suiker</h3>
      <p>Wil je een gladde huid zonder irritatie? Suikerontharing is een zachte en natuurlijke methode voor elk huidtype.</p>
      <ul>
        <li>De haren worden met de groeirichting mee verwijderd</li>
        <li>Geschikt voor de gevoelige huid</li>
        <li>Er wordt enkel natuurlijke suiker gebruikt</li>
        <li>Minder kans op ingegroeide haartjes</li>
        <li>Het resultaat blijft tot vier weken</li>
        <li>Ook geschikt bij couperose en spataders</li>
      </ul>
    </div>
  </div>
  <div class="page right">
    <div class="copy" style="left:8px;width:102px;top:9px">
      <h3>TARIEVEN</h3>
      <ul class="price-list">
        <li><span>Wenkbrauwen</span><span>€9</span></li>
        <li><span>Wenkbrauwen en bovenlip</span><span>€16</span></li>
        <li><span>Bovenlip of kin</span><span>€9</span></li>
        <li><span>Bovenlip en kin</span><span>€16</span></li>
        <li><span>Gezicht</span><span>€25</span></li>
        <li><span>Oksels</span><span>€12</span></li>
        <li><span>Armen</span><span>€20</span></li>
        <li><span>Brazilian bikini of string</span><span>€30</span></li>
        <li><span>Bikinilijn</span><span>€15</span></li>
        <li><span>Onderbenen en knie</span><span>€30</span></li>
        <li><span>Bovenbenen</span><span>€30</span></li>
        <li><span>Volledige benen (zonder bikini)</span><span>€50</span></li>
        <li><span>Volledige benen incl. bikinilijn</span><span>€59</span></li>
      </ul>
      <div class="wordmark" style="text-align:center;font-size:4px;letter-spacing:1.4px;margin-top:14px;color:var(--heading)">Atelier Verano</div>
    </div>
    <div class="photo" role="img" aria-label="Photo of sugaring paste dripping into a jar" style="left:114px;right:0;background:linear-gradient(120deg,#f6eef2,#eadbd6 55%,#e0b88f)"></div>
  </div>
</section>

<!-- Lash extensions -->
<section class="spread is-open" style="left:671px;top:262px">
  <div class="page left grey">
    <div class="outline-box" style="left:16px;top:28px;width:94px;height:79px;padding:5px 6px">
      Lange, volle en gekrulde wimpers dankzij Velura Lashes. Zijden wimpers worden één per één op je eigen wimper geplaatst. Mascara is niet meer nodig en het resultaat oogt heel natuurlijk.
    </div>
    <div class="outline-box" style="left:115px;top:28px;width:86px;height:79px;padding:5px 6px">
      <p>Voordelen van wimperverlenging:</p>
      <ul>
        <li>Tijdsbesparing</li>
        <li>Geen mascara meer</li>
        <li>Waterbestendig</li>
        <li>Natuurlijk resultaat</li>
        <li>Ideaal voor vakantie</li>
        <li>Zachte zijden wimpers</li>
      </ul>
    </div>
    <div class="price-note" style="top:122px">Eerste plaatsing wimperextensions €65<br>Bijwerking na max. 4 weken €35</div>
  </div>
  <div class="page right">
    <div class="photo" role="img" aria-label="Photo of lash extensions being applied with tweezers" style="left:0;right:0;background:linear-gradient(120deg,#e6c3a6,#f0dac9 45%,#dcae8f)"></div>
    <div class="teal-box" style="left:8px;top:99px;width:80px;height:45px;font-size:6.8px;line-height:1.55;text-align:center;padding-top:5px">Individuele Wimperverlenging Velura Lashes</div>
  </div>
</section>

<!-- Lash lifting -->
<section class="spread is-open" style="left:671px;top:473px">
  <div class="page left">
    <div class="photo" role="img" aria-label="Close-up photo of a blue eye with long lashes" style="left:0;right:0;background:linear-gradient(120deg,#e9d5c9,#f3e6de 50%,#d8b8a5)"></div>
    <div class="teal-box" style="left:135px;top:100px;width:78px;height:46px;font-size:6.8px;line-height:1.55;text-align:center;padding-top:10px">Wimperlifting<br>Lumo Lift</div>
  </div>
  <div class="page right grey">
    <div class="outline-box" style="left:47px;top:33px;width:124px;height:85px;padding-top:13px">
      Het hebben van mooie, lange en volle wimpers staat hoog op het verlanglijstje van vele vrouwen. De nieuwe Lumo-methode zorgt in één behandeling van zestig minuten voor gekrulde wimpers, zonder extensions.
    </div>
  </div>
</section>

<!-- Airbrush tanning -->
<section class="spread is-framed" style="left:671px;top:687px">
  <div class="page left">
    <div class="photo" role="img" aria-label="Photo of a tanned body in a bikini" style="left:0;width:105px;background:linear-gradient(120deg,#f3ece8,#d3a47f 50%,#b57a55)"></div>
    <div class="copy" style="left:112px;width:100px;top:9px">
      <h3>Airbrush Tanning</h3>
      <p>Altijd al gedroomd van een natuurlijk bruine huid zonder schadelijke zonnestralen?</p>
      <h3>De Voorbereiding</h3>
      <p>Scrub de huid een dag voordien en breng geen bodylotion of deodorant aan op de dag zelf. Draag losse, donkere kledij.</p>
      <p>De kleur ontwikkelt zich binnen enkele uren en blijft ongeveer een week mooi zichtbaar.</p>
    </div>
  </div>
  <div class="page right">
    <div class="copy" style="left:8px;width:102px;top:9px;height:136px">
      <h3>De Airbrush Tanning Zelf</h3>
      <p>Je huid wordt met een fijne nevel gelijkmatig bespoten. Een sessie duurt ongeveer vijftien minuten.</p>
      <h3 style="margin-top:6px">De Nazorg</h3>
      <p>Wacht acht uur met douchen en vermijd sporten. Gebruik een milde hydraterende lotion voor een langer resultaat.</p>
      <p style="position:absolute;bottom:0">Airbrush tanning voor het volledige lichaam <span style="color:var(--heading)">€29</span></p>
    </div>
    <div class="photo" role="img" aria-label="Portrait photo showing skin before and after tanning" style="left:114px;right:0;background:linear-gradient(90deg,#f4ece9 0%,#e9d2c5 50%,#cf9f82 52%,#f0e7e3 100%)"></div>
  </div>
</section>

</body>
</html>
```